Small butcher shop from Austria needs great powerpoint presentation

We are looking for a powerpoint template for our new CI - it should be modern and clear.

Logo (2 Versions), Slogan, Business Card and Car-Wrap-Design already exist. (See documents below.)

We won't use much text. About 50% of the presentation should be pictures, included in different ways.

We are a family business in Upper Austria, only process animals from farms in the immediate vicinity, produce the products by hand, value animal welfare and short transport routes and avoid packaging as much as possible.

The design should be modern and clear.

Sans Serif

• Use the red color sparingly. Only use sans serif fonts (Myriad Pro - if possible). The logo needs to be on first and last page only.

```html
<!DOCTYPE html>
<html lang="en">
<head>
<meta charset="utf-8">
<title>Halmer Fleischerei – Presentation Template</title>
<link href="https://fonts.googleapis.com/css2?family=Source+Sans+3:wght@400;600;700&display=swap" rel="stylesheet">
<style>
:root{
  --red:#8b1627;
  --red-dark:#6e0f1d;
  --ink:#333333;
  --muted:#6b6b6b;
  --page:#ebebeb;
  --white:#ffffff;
  --chalk:#1e1e1e;
}
*{box-sizing:border-box;margin:0;padding:0}
html,body{width:1200px;height:3831px;overflow:hidden;background:var(--page)}
body{font-family:"Source Sans 3",Arial,sans-serif;color:var(--ink)}
.deck{display:grid;grid-template-columns:553px 553px;grid-auto-rows:310px;gap:30px;padding:33px}
.slide{position:relative;overflow:hidden;background:var(--white)}
.abs{position:absolute}
.photo{position:absolute;background:linear-gradient(135deg,#4a2d28,#8a4a40 55%,#3b2622)}
.ph-dark{background:linear-gradient(135deg,#2a2220,#4c3a33 50%,#231c1a)}
.ph-meat{background:linear-gradient(135deg,#7a2a2a,#c0645c 50%,#6a2424)}
.ph-pink{background:linear-gradient(135deg,#c98c88,#e8b6b0 50%,#b77068)}
.ph-shop{background:linear-gradient(135deg,#3d3a38,#8a7a70 50%,#2e2b29)}
.ph-grey{background:linear-gradient(135deg,#5a5756,#8f8b88 50%,#4a4746)}
.ph-light{background:linear-gradient(135deg,#d8cfc8,#f1ece7 50%,#c4b6aa)}
.title{font-weight:700;font-size:10.5px;letter-spacing:.3px;text-transform:uppercase;color:var(--red)}
.title.light{color:var(--white);font-size:15px}
.rule{width:28px;height:1px;background:var(--red);margin:6px 0 10px}
.rule.light{background:rgba(255,255,255,.8)}
.body{font-size:6.4px;line-height:1.45;color:var(--muted)}
.body.light{color:rgba(255,255,255,.9)}
.body.red{color:var(--red)}
.brand{display:flex;align-items:center;justify-content:center;font-weight:700;font-size:16px;letter-spacing:1px;color:var(--white)}
.brand.box{background:var(--red);width:68px;height:72px}
.brand.ink{color:var(--red)}
.socials{display:flex;gap:8px}
.socials span{width:12px;height:12px;border-radius:50%;background:var(--white)}
.btn{display:inline-block;font-size:6px;font-weight:700;padding:3px 8px}
.btn.white{background:var(--white);color:var(--red)}
.btn.red{background:var(--red);color:var(--white)}
.caption{position:absolute;left:0;right:0;text-align:center;font-size:7px;color:var(--white)}
.price{position:absolute;left:0;bottom:6px;background:var(--red);color:var(--white);font-size:6px;font-weight:700;padding:2px 4px}
.toc li{list-style:none;font-size:6px;color:rgba(255,255,255,.85);margin-bottom:15px}
.num{display:inline-block;background:var(--red);color:var(--white);font-size:7.5px;font-weight:700;padding:2px 4px}
.icon-set{fill:var(--red)}
.cuts-chart{background:radial-gradient(ellipse at 45% 50%,#5c5c5c,#3a3a3a 55%,#262626 85%);border:1px solid rgba(255,255,255,.35);border-radius:38% 42% 30% 34%}
.contact{display:flex;align-items:center;gap:10px;font-size:8px;color:var(--white);margin-bottom:6px}
.contact svg{width:10px;height:10px}
</style>
</head>
<body>
<main class="deck">

<!-- 1 Cover -->
<section class="slide">
  <div class="photo ph-dark" style="inset:0" role="img" aria-label="Cured meats, olives and nuts on a dark table"></div>
  <div class="abs" style="inset:0;background:rgba(25,18,16,.45)"></div>
  <div class="abs brand box" style="left:37px;top:56px">HALMER</div>
  <div class="abs" style="left:37px;top:145px;width:170px">
    <div class="title light" style="font-size:13px">Lorem ipsum dolor</div>
    <div class="rule light"></div>
    <p class="body light">Lorem ipsum dolor sit amet, consectetuer adipiscing elit, sed diam nonummy nibh euismod tincidunt ut laoreet dolore magna aliquam volutpat. Ut wisi</p>
  </div>
  <div class="abs socials" style="left:37px;top:242px"><span></span><span></span><span></span></div>
</section>

<!-- 2 Cover alt -->
<section class="slide">
  <div class="abs brand ink" style="left:0;right:0;top:0;height:79px">HALMER</div>
  <div class="photo ph-dark" style="left:0;right:0;top:79px;bottom:0" role="img" aria-label="Charcuterie platter with olives and bread"></div>
  <div class="abs" style="left:0;right:0;top:79px;bottom:0;background:rgba(25,18,16,.5)"></div>
  <div class="abs" style="left:140px;right:140px;top:140px;text-align:center">
    <div class="title light" style="font-size:17px">Lorem ipsum dolor</div>
    <p class="body light" style="margin-top:10px">Lorem ipsum dolor sit amet, consectetuer adipiscing elit, sed diam nonummy nibh euismod tincidunt ut laoreet dolore magna aliquam volutpat. Ut wisi enim ad minim veniam, quis nostrud exerci tation ullamcorper suscipit lobortis nisl ut aliquip ex ea</p>
  </div>
  <div class="abs socials" style="left:250px;top:270px"><span></span><span></span><span></span></div>
</section>

<!-- 3 Table of content -->
<section class="slide">
  <div class="photo ph-meat" style="inset:0" role="img" aria-label="Sliced salami, cheese and cucumber on a wooden board"></div>
  <div class="abs" style="left:280px;right:0;top:0;bottom:0;background:linear-gradient(90deg,rgba(40,30,28,0),rgba(40,30,28,.85) 25%)"></div>
  <div class="abs" style="left:348px;top:60px">
    <div class="title light" style="font-size:12px">Table of content</div>
    <div class="rule light"></div>
    <ul class="toc" style="margin-top:12px">
      <li>Market Overview</li><li>Concept</li><li>Experience Packages</li><li>Experience Formula</li><li>Teach Formula</li><li>Loyalty Formula</li><li>Who We Are</li>
    </ul>
  </div>
</section>

<!-- 4 Diagonal photo -->
<section class="slide">
  <div class="abs" style="left:31px;top:73px;width:240px">
    <div class="title">Lorem ipsum dolor sit amet</div>
    <div class="rule"></div>
    <p class="body">Lorem ipsum dolor sit amet, consectetuer adipiscing elit, sed diam nonummy nibh euismod tincidunt ut laoreet dolore magna aliquam volutpat. Ut wisi enim ad minim veniam, quis nostrud exerci tation ullamcorper suscipit lobortis nisl ut aliquip ex ea commodo consequat. Duis autem vel eum iriure dolor in hendrerit in vulputate velit esse</p>
    <p class="body red" style="margin:5px 0">Lorem ipsum dolor sit amet, consectetuer</p>
    <p class="body">Lorem ipsum dolor sit amet, consectetuer adipiscing elit, sed diam nonummy nibh euismod tincidunt ut laoreet dolore magna aliquam volutpat. Ut wisi enim ad minim veniam, quis nostrud</p>
  </div>
  <div class="photo ph-shop" style="left:230px;right:0;top:0;bottom:0;clip-path:polygon(37% 0,100% 0,100% 100%,0 100%)" role="img" aria-label="Butcher at work in front of a meat counter"></div>
</section>

<!-- 5 Red band with photo -->
<section class="slide">
  <div class="abs" style="left:0;top:0;bottom:0;width:82px;background:var(--red)"></div>
  <div class="photo ph-dark" style="left:40px;top:33px;width:244px;height:244px" role="img" aria-label="Wine bottle with antipasti on a wooden table"></div>
  <div class="abs" style="left:333px;top:122px;width:190px">
    <div class="title">Lorem ipsum dolor sit amet</div>
    <div class="rule"></div>
    <p class="body">Lorem ipsum dolor sit amet, consectetuer adipiscing elit, sed diam nonummy nibh euismod tincidunt ut laoreet dolore magna aliquam volutpat. Ut wisi enim ad minim veniam, quis nostrud exerci tation ullamcorper suscipit lobortis nisl ut aliquip ex</p>
  </div>
</section>

<!-- 6 Portrait plus three -->
<section class="slide">
  <div class="photo ph-shop" style="left:0;top:0;bottom:0;width:178px" role="img" aria-label="Butcher in apron standing in the shop"></div>
  <div class="abs" style="left:205px;top:58px;width:320px">
    <div class="title">Lorem ipsum dolor sit amet</div>
    <div class="rule"></div>
    <p class="body">Lorem ipsum dolor sit amet, consectetuer adipiscing elit, sed diam nonummy nibh euismod tincidunt ut laoreet dolore magna aliquam volutpat. Ut wisi enim ad minim veniam, quis</p>
  </div>
  <div class="photo ph-meat" style="left:205px;top:131px;width:100px;height:129px" role="img" aria-label="Raw beef with wine"></div>
  <div class="photo ph-pink" style="left:314px;top:131px;width:100px;height:129px" role="img" aria-label="Sliced ham"></div>
  <div class="photo ph-pink" style="left:423px;top:131px;width:100px;height:129px" role="img" aria-label="Fresh sausages"></div>
</section>

<!-- 7 Section cover -->
<section class="slide">
  <div class="photo ph-dark" style="inset:0" role="img" aria-label="Pork chop on a cutting board with tomatoes, garlic and spices"></div>
  <div class="abs brand box" style="left:449px;top:92px">HALMER</div>
  <div class="abs" style="left:400px;top:187px;width:140px;text-align:right">
    <div class="title light" style="font-size:12px">Lorem ipsum<br><span style="font-weight:400">dolor sit amet</span></div>
    <p class="body light" style="font-size:8px;margin-top:8px">Lorem ipsum dolor sit amet consectetuer adipiscing elit,</p>
  </div>
</section>

<!-- 8 Numbered list -->
<section class="slide">
  <div class="abs" style="left:0;top:0;bottom:0;width:216px;background:var(--red)"></div>
  <div class="abs" style="left:32px;top:136px;width:160px">
    <div class="title" style="color:var(--white)">Lorem ipsum dolor sit amet</div>
    <div class="rule light"></div>
    <p class="body light">Lorem ipsum dolor sit amet, consectetuer adipiscing elit, sed diam nonummy nibh euismod tincidunt ut</p>
  </div>
  <div class="photo ph-pink" style="left:216px;top:0;width:136px;height:101px" role="img" aria-label="Sliced roast ham"></div>
  <div class="photo ph-meat" style="left:216px;top:105px;width:136px;height:100px" role="img" aria-label="Smoked sausages"></div>
  <div class="photo ph-dark" style="left:216px;top:209px;width:136px;height:101px" role="img" aria-label="Dry cured salami"></div>
  <div class="abs" style="left:372px;top:50px;width:150px">
    <span class="num">01</span><p class="body" style="margin-top:12px">Lorem ipsum dolor sit amet, consectetuer adipiscing elit, sed diam nonummy nibh</p>
  </div>
  <div class="abs" style="left:372px;top:129px;width:150px">
    <span class="num">02</span><p class="body" style="margin-top:12px">Lorem ipsum dolor sit amet, consectetuer adipiscing elit, sed diam nonummy nibh</p>
  </div>
  <div class="abs" style="left:372px;top:211px;width:150px">
    <span class="num">03</span><p class="body" style="margin-top:12px">Lorem ipsum dolor sit amet, consectetuer adipiscing elit, sed diam nonummy nibh</p>
  </div>
</section>

<!-- 9 Collage right -->
<section class="slide">
  <div class="abs" style="left:31px;top:112px;width:120px">
    <div class="title">Lorem ipsum<br>dolor sit amet</div>
    <div class="rule"></div>
    <p class="body">Lorem ipsum dolor sit amet, consectetuer adipiscing elit, sed diam nonummy nibh euismod tincidunt ut laoreet dolore magna aliquam volutpat. Ut wisi enim ad</p>
  </div>
  <div class="photo ph-dark" style="left:178px;top:33px;width:109px;height:245px" role="img" aria-label="Steak on crushed ice"></div>
  <div class="photo ph-light" style="left:294px;top:33px;width:228px;height:123px" role="img" aria-label="Butcher cutting meat at a counter"></div>
  <div class="photo ph-meat" style="left:294px;top:164px;width:110px;height:114px" role="img" aria-label="Butcher trimming a rack of ribs"></div>
  <div class="photo ph-shop" style="left:412px;top:164px;width:110px;height:114px" role="img" aria-label="Meat being prepared in the workshop"></div>
</section>

<!-- 10 Collage left -->
<section class="slide">
  <div class="photo ph-shop" style="left:33px;top:36px;width:235px;height:113px" role="img" aria-label="Display counter full of meat"></div>
  <div class="photo ph-pink" style="left:275px;top:36px;width:118px;height:113px" role="img" aria-label="Thinly sliced ham"></div>
  <div class="photo ph-grey" style="left:400px;top:36px;width:122px;height:239px" role="img" aria-label="Butcher with a knife at the counter"></div>
  <div class="photo ph-dark" style="left:275px;top:159px;width:118px;height:116px" role="img" aria-label="Salami with olives"></div>
  <div class="abs" style="left:33px;top:190px;width:220px">
    <div class="title">Lorem ipsum<br>dolor sit amet</div>
    <div class="rule"></div>
    <p class="body">Lorem ipsum dolor sit amet, consectetuer adipiscing elit, sed diam nonummy nibh euismod tincidunt ut laoreet dolorenum magna aliquam volutpat. Ut wisi enim ad minim veniam, quis</p>
  </div>
</section>

<!-- 11 Section cover centered -->
<section class="slide">
  <div class="photo ph-grey" style="inset:0" role="img" aria-label="Grilled steaks and vegetables on a grey stone table"></div>
  <div class="abs brand box" style="left:244px;top:62px">HALMER</div>
  <div class="abs" style="left:0;right:0;top:182px;text-align:center">
    <div class="title light" style="font-size:12px">Lorem ipsum dolor sit amet</div>
    <p class="body light" style="font-size:8.5px;margin-top:4px">Lorem ipsum dolor sit amet consectetuer adipiscing</p>
  </div>
</section>

<!-- 12 Four photos -->
<section class="slide">
  <div class="photo ph-dark" style="left:33px;top:36px;width:235px;height:119px" role="img" aria-label="Hams hanging in a smoke room"><span class="caption" style="top:96px">Lorem ipsum dolor sit amet</span></div>
  <div class="photo ph-meat" style="left:281px;top:36px;width:235px;height:119px" role="img" aria-label="Sliced roast beef"><span class="caption" style="top:96px">Lorem ipsum dolor sit amet</span></div>
  <div class="photo ph-shop" style="left:33px;top:168px;width:235px;height:119px" role="img" aria-label="Butcher at a cutting table"><span class="caption" style="top:96px">Lorem ipsum dolor sit amet</span></div>
  <div class="photo ph-pink" style="left:281px;top:168px;width:235px;height:119px" role="img" aria-label="Raw chicken on a board"><span class="caption" style="top:96px">Lorem ipsum dolor sit amet</span></div>
</section>

<!-- 13 Delivery van -->
<section class="slide">
  <div class="photo ph-grey" style="inset:0" role="img" aria-label="Delivery van parked in front of a farm building"></div>
  <div class="abs" style="inset:0;background:rgba(139,22,39,.35);clip-path:polygon(0 0,48% 0,34% 50%,48% 100%,0 100%)"></div>
  <div class="abs" style="inset:0;background:var(--red);clip-path:polygon(0 0,28% 0,42% 50%,28% 100%,0 100%)"></div>
  <div class="abs" style="left:33px;top:128px;width:160px">
    <div class="title light" style="font-size:12px">Lorem ipsum dolor</div>
    <div class="rule light"></div>
    <p class="body light">Lorem ipsum dolor sit amet, consectetuer adipiscing elit, sed diam nonummy nibh euismod tincidunt ut</p>
    <span class="btn white" style="margin-top:8px">Lorem ipsum dolor</span>
  </div>
</section>

<!-- 14 Price grid -->
<section class="slide">
  <div class="abs" style="left:0;right:0;top:33px;text-align:center"><div class="title">Lorem ipsum dolor sit amet</div><div class="rule" style="margin:6px auto"></div></div>
  <div class="abs" style="left:33px;top:64px;display:grid;grid-template-columns:repeat(4,114px);grid-auto-rows:92px;column-gap:10px;row-gap:16px">
    <div class="photo ph-dark" style="position:relative" role="img" aria-label="Grilled meat platter"><span class="price">5.99$</span><span class="caption" style="top:80px;left:30px">Lorem ipsum dolor</span></div>
    <div class="photo ph-meat" style="position:relative" role="img" aria-label="Raw beef cuts"><span class="price">5.99$</span><span class="caption" style="top:80px;left:30px">Lorem ipsum dolor</span></div>
    <div class="photo ph-pink" style="position:relative" role="img" aria-label="Sliced sausage platter"><span class="price">5.99$</span><span class="caption" style="top:80px;left:30px">Lorem ipsum dolor</span></div>
    <div class="photo ph-meat" style="position:relative" role="img" aria-label="Minced meat"><span class="price">5.99$</span><span class="caption" style="top:80px;left:30px">Lorem ipsum dolor</span></div>
    <div class="photo ph-dark" style="position:relative" role="img" aria-label="Grilled meat platter"><span class="price">5.99$</span><span class="caption" style="top:80px;left:30px">Lorem ipsum dolor</span></div>
    <div class="photo ph-meat" style="position:relative" role="img" aria-label="Raw beef cuts"><span class="price">5.99$</span><span class="caption" style="top:80px;left:30px">Lorem ipsum dolor</span></div>
    <div class="photo ph-pink" style="position:relative" role="img" aria-label="Sliced sausage platter"><span class="price">5.99$</span><span class="caption" style="top:80px;left:30px">Lorem ipsum dolor</span></div>
    <div class="photo ph-meat" style="position:relative" role="img" aria-label="Minced meat"><span class="price">5.99$</span><span class="caption" style="top:80px;left:30px">Lorem ipsum dolor</span></div>
  </div>
</section>

<!-- 15 Header photo with framed cards -->
<section class="slide">
  <div class="photo ph-meat" style="left:0;right:0;top:0;height:178px" role="img" aria-label="Assorted raw meat cuts"></div>
  <div class="abs" style="left:0;right:0;top:0;height:178px;background:linear-gradient(90deg,rgba(110,15,29,.85),rgba(60,20,20,.55))"></div>
  <div class="abs" style="left:37px;top:38px;width:200px">
    <div class="title light" style="font-size:12px">Lorem ipsum dolor</div>
    <div class="rule light"></div>
    <p class="body light">Lorem ipsum dolor sit amet, consectetuer adipiscing elit, sed diam nonummy nibh euismod tincidunt ut</p>
    <span class="btn red" style="margin-top:6px">Lorem ipsum dolor</span>
  </div>
  <div class="photo ph-meat" style="left:37px;top:134px;width:153px;height:116px;border:3px solid var(--white)" role="img" aria-label="Minced beef on paper"></div>
  <div class="photo ph-dark" style="left:202px;top:134px;width:152px;height:116px;border:3px solid var(--white)" role="img" aria-label="Platter of mixed meats"></div>
  <div class="photo ph-meat" style="left:367px;top:134px;width:153px;height:116px;border:3px solid var(--white)" role="img" aria-label="Meat counter display"></div>
  <div class="abs body" style="left:37px;top:258px;width:153px;text-align:center"><b>Lorem ipsum dolor</b><br>Lorem ipsum dolor sit amet, consectetuer</div>
  <div class="abs body" style="left:202px;top:258px;width:152px;text-align:center"><b>Lorem ipsum dolor</b><br>Lorem ipsum dolor sit amet, consectetuer</div>
  <div class="abs body" style="left:367px;top:258px;width:153px;text-align:center"><b>Lorem ipsum dolor</b><br>Lorem ipsum dolor sit amet, consectetuer</div>
</section>

<!-- 16 Four products with buttons -->
<section class="slide">
  <div class="abs" style="left:100px;right:100px;top:33px;text-align:center">
    <div class="title">Lorem ipsum dolor sit amet</div><div class="rule" style="margin:6px auto"></div>
    <p class="body">Lorem ipsum dolor sit amet, consectetuer adipiscing elit, sed diam nonummy nibh euismod tincidunt ut laoreet dolorenum</p>
  </div>
  <div class="abs" style="left:31px;top:98px;display:grid;grid-template-columns:repeat(4,115px);column-gap:9px">
    <div><div class="photo ph-dark" style="position:relative;height:92px" role="img" aria-label="Grilled meat platter"><span class="caption" style="top:80px">Lorem ipsum dolor</span></div><p class="body" style="margin:7px 8px">Lorem ipsum dolor sit ametit consectet adipiscing elit, sed diam nonummy nib euismod tincidunt ut laoreet doloremi</p><div style="text-align:center"><span class="btn red">Lorem ipsum</span></div></div>
    <div><div class="photo ph-meat" style="position:relative;height:92px" role="img" aria-label="Raw beef cuts"><span class="caption" style="top:80px">Lorem ipsum dolor</span></div><p class="body" style="margin:7px 8px">Lorem ipsum dolor sit ametit consectet adipiscing elit, sed diam nonummy nib euismod tincidunt ut laoreet doloremi</p><div style="text-align:center"><span class="btn red">Lorem ipsum</span></div></div>
    <div><div class="photo ph-pink" style="position:relative;height:92px" role="img" aria-label="Sliced sausage platter"><span class="caption" style="top:80px">Lorem ipsum dolor</span></div><p class="body" style="margin:7px 8px">Lorem ipsum dolor sit ametit consectet adipiscing elit, sed diam nonummy nib euismod tincidunt ut laoreet doloremi</p><div style="text-align:center"><span class="btn red">Lorem ipsum</span></div></div>
    <div><div class="photo ph-meat" style="position:relative;height:92px" role="img" aria-label="Minced meat"><span class="caption" style="top:80px">Lorem ipsum dolor</span></div><p class="body" style="margin:7px 8px">Lorem ipsum dolor sit ametit consectet adipiscing elit, sed diam nonummy nib euismod tincidunt ut laoreet doloremi</p><div style="text-align:center"><span class="btn red">Lorem ipsum</span></div></div>
  </div>
</section>

<!-- 17 Text two columns -->
<section class="slide">
  <div class="photo ph-light" style="left:0;top:0;bottom:0;width:183px" role="img" aria-label="Table with cold cuts and honey"></div>
  <div class="abs" style="left:223px;top:55px;width:300px">
    <div class="title">Lorem ipsum dolor sit amet</div>
    <div class="rule"></div>
    <div style="display:grid;grid-template-columns:1fr 1fr;column-gap:18px">
      <p class="body">Lorem ipsum dolor sit amet, consectet adipiscing elit, sed diam nonummy nib euismod tincidunt ut laoreet dolore magna aliquam erat volutpat. Ut wisi enim ad minim veniam, quis nostrud exerci tati ullamcorper suscipit lobortis nisl ut ali ex ea commodo consequat. Duis auten vel eum iriure dolor in hendrerit in vuli velit esse molestie consequat, vel illum dolore eu feugiat nulla facilisis at vero eros et accumsan et iusto odio dignissi qui blandit praesent luptatum zzril del augue duis dolore te feugait nulla facili. Lorem ipsum dolor sit amet, cons ectet adipiscing elit, sed diam nonummy nib euismod tincidunt ut laoreet dolore mi aliquam erat volutpat. Ut wisi enim ad minim veniam, quis nostrud exerci tati ullamcorper suscipit lobortis nisl ut ali ex ea commodo consequat.</p>
      <p class="body">Lorem ipsum dolor sit amet, consectet adipiscing elit, sed diam nonummy nib euismod tincidunt ut laoreet dolore magna aliquam erat volutpat. Ut wisi enim ad minim veniam, quis nostrud exerci tati ullamcorper suscipit lobortis nisl ut ali ex ea commodo consequat. Duis auten vel eum iriure dolor in hendrerit in vuli velit esse molestie consequat, vel illum dolore eu feugiat nulla facilisis at vero eros et accumsan et iusto odio dignissi qui blandit praesent luptatum zzril del augue duis dolore te feugait nulla facili. Lorem ipsum dolor sit amet, cons ectet adipiscing elit, sed diam nonummy nib euismod tincidunt ut laoreet dolore mi aliquam erat volutpat. Ut wisi enim ad minim veniam, quis nostrud exerci tati ullamcorper suscipit lobortis nisl ut ali ex ea commodo consequat.</p>
    </div>
  </div>
</section>

<!-- 18 Photo with overlay panels -->
<section class="slide">
  <div class="photo ph-light" style="left:0;top:0;bottom:0;width:367px" role="img" aria-label="Cheese, ham and bread on a rustic table"></div>
  <div class="abs" style="left:183px;top:0;bottom:0;width:184px;background:rgba(255,255,255,.72)"></div>
  <div class="abs" style="left:367px;top:0;bottom:0;right:0;background:var(--red)"></div>
  <div class="abs" style="left:212px;top:55px;width:130px">
    <div class="title">Lorem ipsum dolor sit</div><div class="rule"></div>
    <p class="body">Lorem ipsum dolor sit amet, consectet adipiscing elit, sed diam nonummy nib euismod tincidunt ut laoreet dolore aliquam erat volutpat. Ut wisi enim ad minim veniam, quis nostrud exerci tati ullamcorper suscipit lobortis nisl ut ali ex ea commodo consequat. Duis auten vel eum iriure dolor in hendrerit in vuli velit esse molestie consequat, vel illum dolore eu feugiat nulla facilisis at vero eros et accumsan et iusto odio dignissi qui blandit praesent luptatum zzril del augue duis dolore te feugait nulla facili. Lorem ipsum dolor sit amet, cons ectet adipiscing elit, sed diam nonummy nib euismod tincidunt ut laoreet dolore aliquam erat volutpat.</p>
  </div>
  <div class="abs" style="left:393px;top:55px;width:130px">
    <div class="title" style="color:var(--white)">Lorem ipsum dolor sit</div><div class="rule light"></div>
    <p class="body light">Lorem ipsum dolor sit amet, consectet adipiscing elit, sed diam nonummy nib euismod tincidunt ut laoreet dolore aliquam erat volutpat. Ut wisi enim ad minim veniam, quis nostrud exerci tati ullamcorper suscipit lobortis nisl ut ali ex ea commodo consequat. Duis auten vel eum iriure dolor in hendrerit in vuli velit esse molestie consequat, vel illum dolore eu feugiat nulla facilisis at vero eros et accumsan et iusto odio dignissi qui blandit praesent luptatum zzril del augue duis dolore te feugait nulla facili. Lorem ipsum dolor sit amet, cons ectet adipiscing elit, sed diam nonummy nib euismod tincidunt ut laoreet dolore aliquam erat volutpat.</p>
  </div>
</section>

<!-- 19 Full collage -->
<section class="slide">
  <div class="photo ph-dark" style="left:0;top:0;width:222px;height:180px" role="img" aria-label="Antipasti board with olives and cheese"></div>
  <div class="photo ph-pink" style="left:226px;top:0;width:160px;height:180px" role="img" aria-label="Roast ham with spring onion"></div>
  <div class="photo ph-dark" style="left:390px;top:0;right:0;height:83px" role="img" aria-label="Salami and rosemary"></div>
  <div class="photo ph-shop" style="left:390px;top:88px;right:0;height:92px" role="img" aria-label="Meat counter"></div>
  <div class="photo ph-meat" style="left:0;top:184px;width:222px;bottom:0" role="img" aria-label="Sliced grilled steak"></div>
  <div class="photo ph-shop" style="left:226px;top:184px;right:0;bottom:0" role="img" aria-label="Butchers working together at the counter"></div>
</section>

<!-- 20 Cuts chart -->
<section class="slide" style="background:var(--chalk)">
  <div class="abs" style="left:150px;right:150px;top:33px;text-align:center">
    <div class="title" style="font-size:8.5px">Lorem ipsum dolor sit amet</div>
    <div class="rule" style="margin:6px auto"></div>
    <p class="body light">Lorem ipsum dolor sit amet, consectetuer adipiscing elit, sed diam nonummy nibh euismod tincidunt ut laoreet dolorenum</p>
  </div>
  <div class="abs cuts-chart" role="img" aria-label="Chalk drawing of beef cuts on a cow outline" style="left:140px;top:112px;width:280px;height:160px"></div>
</section>

<!-- 21 Icon set -->
<section class="slide">
  <svg class="abs icon-set" style="left:66px;top:38px" width="420" height="240" viewBox="0 0 420 240" role="img" aria-label="Set of food and drink icons">
    <defs>
      <symbol id="i-cup" viewBox="0 0 14 14"><path d="M2 4h8v5a3 3 0 0 1-3 3H5a3 3 0 0 1-3-3z"/><path d="M10 5h2.5v3H10z"/></symbol>
      <symbol id="i-bottle" viewBox="0 0 14 14"><path d="M6 1h2v3l1.5 2v7h-5V6L6 4z"/></symbol>
      <symbol id="i-glass" viewBox="0 0 14 14"><path d="M3 1h8l-.5 4.5A3.5 3.5 0 0 1 7.6 8.8V12H10v1.2H4V12h2.4V8.8A3.5 3.5 0 0 1 3.5 5.5z"/></symbol>
      <symbol id="i-fork" viewBox="0 0 14 14"><path d="M4 1h1v4h1V1h1v4h1V1h1v5a2 2 0 0 1-2 2v5.5H6V8a2 2 0 0 1-2-2z"/></symbol>
      <symbol id="i-plate" viewBox="0 0 14 14"><path fill-rule="evenodd" d="M7 1a6 6 0 1 1 0 12A6 6 0 0 1 7 1zm0 2.5a3.5 3.5 0 1 0 0 7 3.5 3.5 0 0 0 0-7z"/></symbol>
      <symbol id="i-apple" viewBox="0 0 14 14"><circle cx="7" cy="8.5" r="4.5"/><path d="M7 4l2-3h1.2L8 4z"/></symbol>
      <symbol id="i-cake" viewBox="0 0 14 14"><path d="M1 12.5L7 3l6 9.5z"/></symbol>
      <symbol id="i-pot" viewBox="0 0 14 14"><path d="M1 5h12v1.3H1z"/><path d="M2.5 7h9v4a2 2 0 0 1-2 2h-5a2 2 0 0 1-2-2z"/><path d="M6 3h2v1.5H6z"/></symbol>
      <symbol id="i-cone" viewBox="0 0 14 14"><circle cx="7" cy="4.5" r="3.5"/><path d="M3.8 6.5h6.4L7 13.5z"/></symbol>
      <symbol id="i-burger" viewBox="0 0 14 14"><path d="M2 6a5 4 0 0 1 10 0z"/><rect x="1.5" y="7" width="11" height="1.6" rx=".8"/><path d="M2 9.5h10v1.5a1.5 1.5 0 0 1-1.5 1.5h-7A1.5 1.5 0 0 1 2 11z"/></symbol>
      <symbol id="i-cherry" viewBox="0 0 14 14"><circle cx="4" cy="10" r="2.8"/><circle cx="10" cy="10" r="2.8"/><path d="M4 7.5L8 1.5h1L5 7.8zM10 7.5L8.6 2h.9l1.4 5.6z"/></symbol>
      <symbol id="i-knife" viewBox="0 0 14 14"><path d="M2 12L10 2.5c1.5 1 1.5 3 0 5L5 10.5 3.2 13z"/></symbol>
    </defs>
    <g>
      <use href="#i-fork" x="0" y="0" width="14" height="14"/><use href="#i-bottle" x="49" y="0" width="14" height="14"/><use href="#i-cup" x="98" y="0" width="14" height="14"/><use href="#i-burger" x="147" y="0" width="14" height="14"/><use href="#i-pot" x="196" y="0" width="14" height="14"/><use href="#i-cup" x="245" y="0" width="14" height="14"/><use href="#i-glass" x="294" y="0" width="14" height="14"/><use href="#i-plate" x="343" y="0" width="14" height="14"/><use href="#i-knife" x="392" y="0" width="14" height="14"/>
      <use href="#i-cherry" x="0" y="32" width="14" height="14"/><use href="#i-fork" x="49" y="32" width="14" height="14"/><use href="#i-pot" x="98" y="32" width="14" height="14"/><use href="#i-bottle" x="147" y="32" width="14" height="14"/><use href="#i-burger" x="196" y="32" width="14" height="14"/><use href="#i-cone" x="245" y="32" width="14" height="14"/><use href="#i-cup" x="294" y="32" width="14" height="14"/><use href="#i-glass" x="343" y="32" width="14" height="14"/><use href="#i-apple" x="392" y="32" width="14" height="14"/>
      <use href="#i-bottle" x="0" y="64" width="14" height="14"/><use href="#i-apple" x="49" y="64" width="14" height="14"/><use href="#i-glass" x="98" y="64" width="14" height="14"/><use href="#i-cake" x="147" y="64" width="14" height="14"/><use href="#i-fork" x="196" y="64" width="14" height="14"/><use href="#i-cake" x="245" y="64" width="14" height="14"/><use href="#i-knife" x="294" y="64" width="14" height="14"/><use href="#i-bottle" x="343" y="64" width="14" height="14"/><use href="#i-pot" x="392" y="64" width="14" height="14"/>
      <use href="#i-burger" x="0" y="96" width="14" height="14"/><use href="#i-glass" x="49" y="96" width="14" height="14"/><use href="#i-cone" x="98" y="96" width="14" height="14"/><use href="#i-apple" x="147" y="96" width="14" height="14"/><use href="#i-glass" x="196" y="96" width="14" height="14"/><use href="#i-plate" x="245" y="96" width="14" height="14"/><use href="#i-cherry" x="294" y="96" width="14" height="14"/><use href="#i-cup" x="343" y="96" width="14" height="14"/><use href="#i-bottle" x="392" y="96" width="14" height="14"/>
      <use href="#i-glass" x="0" y="128" width="14" height="14"/><use href="#i-cake" x="49" y="128" width="14" height="14"/><use href="#i-bottle" x="98" y="128" width="14" height="14"/><use href="#i-pot" x="147" y="128" width="14" height="14"/><use href="#i-apple" x="196" y="128" width="14" height="14"/><use href="#i-cup" x="245" y="128" width="14" height="14"/><use href="#i-burger" x="294" y="128" width="14" height="14"/><use href="#i-knife" x="343" y="128" width="14" height="14"/><use href="#i-apple" x="392" y="128" width="14" height="14"/>
      <use href="#i-pot" x="0" y="160" width="14" height="14"/><use href="#i-cherry" x="49" y="160" width="14" height="14"/><use href="#i-cup" x="98" y="160" width="14" height="14"/><use href="#i-knife" x="147" y="160" width="14" height="14"/><use href="#i-cone" x="196" y="160" width="14" height="14"/><use href="#i-bottle" x="245" y="160" width="14" height="14"/><use href="#i-cup" x="294" y="160" width="14" height="14"/><use href="#i-pot" x="343" y="160" width="14" height="14"/><use href="#i-cake" x="392" y="160" width="14" height="14"/>
      <use href="#i-apple" x="0" y="192" width="14" height="14"/><use href="#i-knife" x="49" y="192" width="14" height="14"/><use href="#i-plate" x="98" y="192" width="14" height="14"/><use href="#i-glass" x="147" y="192" width="14" height="14"/><use href="#i-burger" x="196" y="192" width="14" height="14"/><use href="#i-apple" x="245" y="192" width="14" height="14"/><use href="#i-fork" x="294" y="192" width="14" height="14"/><use href="#i-cone" x="343" y="192" width="14" height="14"/><use href="#i-cherry" x="392" y="192" width="14" height="14"/>
      <use href="#i-cup" x="0" y="224" width="14" height="14"/><use href="#i-plate" x="49" y="224" width="14" height="14"/><use href="#i-apple" x="98" y="224" width="14" height="14"/><use href="#i-plate" x="147" y="224" width="14" height="14"/><use href="#i-cup" x="196" y="224" width="14" height="14"/><use href="#i-bottle" x="245" y="224" width="14" height="14"/><use href="#i-apple" x="294" y="224" width="14" height="14"/><use href="#i-glass" x="343" y="224" width="14" height="14"/><use href="#i-knife" x="392" y="224" width="14" height="14"/>
    </g>
  </svg>
</section>

<!-- 22 Closing -->
<section class="slide" style="background:var(--red)">
  <div class="abs brand" style="left:0;right:0;top:88px;font-size:20px">HALMER</div>
  <div class="abs" style="left:200px;top:148px">
    <div class="title light" style="font-size:12px">Lorem ipsum dolor</div>
    <div style="margin-top:8px">
      <div class="contact"><svg viewBox="0 0 10 10" fill="none" stroke="#fff" stroke-width="1"><rect x="1" y="2" width="8" height="6"/><path d="M1 2l4 3 4-3"/></svg>Lorem Ipsum Dolor Sit Amet</div>
      <div class="contact"><svg viewBox="0 0 10 10" fill="none" stroke="#fff" stroke-width="1"><circle cx="5" cy="5" r="4"/><path d="M1 5h8M5 1c-2 2-2 6 0 8M5 1c2 2 2 6 0 8"/></svg>Lorem Ipsum Dolor Sit Amet</div>
      <div class="contact"><svg viewBox="0 0 10 10" fill="none" stroke="#fff" stroke-width="1"><rect x="3" y="1" width="4" height="8" rx="1"/></svg>Lorem Ipsum Dolor Sit Amet</div>
      <div class="contact"><svg viewBox="0 0 10 10" fill="none" stroke="#fff" stroke-width="1"><path d="M5 9S2 6 2 4a3 3 0 016 0c0 2-3 5-3 5z"/><circle cx="5" cy="4" r="1"/></svg>Lorem Ipsum Dolor Sit Amet</div>
    </div>
  </div>
  <div class="abs socials" style="left:255px;top:262px"><span></span><span></span><span></span></div>
</section>

</main>
</body>
</html>
```